Career Development Skills | Business Card & Logo Design

We are looking for a business card including logo design for a new Sydney based business called 'Bright Pathwork'.
We offer a range of services that focus on building the Employability or Employment skills for individuals focusing on job seekers and those interested in building skills required to develop their career. Employability skills are required not only to gain employment, but also to progress within an organisation so as to achieve one's potential.
Updates
Target Market(s)
Our client targets include corporates and govt agencies looking to build skills within their current employee base or assist staff in the transition between roles or workplaces.
Industry/Entity Type
Business
Look and feel
Each slider illustrates characteristics of the customer's brand and the style your logo design should communicate.

```html
<!DOCTYPE html>
<html lang="en">
<head>
<meta charset="utf-8">
<title>Bright Pathwork – Business Card</title>
<link rel="stylesheet" href="https://fonts.googleapis.com/css2?family=Cinzel:wght@700&family=Pathway+Gothic+One&display=swap">
<style>
  :root {
    --stage: #1b1b1b;
    --card-dark: #242424;
    --card-light: #3c3c3c;
    --card-edge: #555;
    --teal: #1fa3a3;
    --amber: #f0a21c;
    --silver: #c9c9c9;
    --grey-text: #8a8a8a;
    --faint: #4a4a4a;
  }
  * { margin: 0; padding: 0; box-sizing: border-box; }
  html, body {
    width: 1200px; height: 1164px; overflow: hidden;
    background: var(--stage);
  }
  .canvas { position: relative; width: 1200px; height: 1164px; }
  .card {
    position: absolute;
    width: 730px; height: 448px;
    border: 1px solid var(--card-edge);
    overflow: hidden;
  }
  .card--front {
    left: 76px; top: 55px;
    background: linear-gradient(200deg, var(--card-light) 0%, var(--card-dark) 70%);
  }
  .card--back {
    left: 412px; top: 556px;
    background: linear-gradient(160deg, #2b2b2b 0%, var(--card-dark) 100%);
  }
  .brand-lockup {
    position: absolute; left: 0; top: 150px; width: 100%;
    display: flex; justify-content: center; align-items: center; gap: 14px;
  }
  .brand-dot {
    width: 18px; height: 18px; border-radius: 50%; background: var(--teal);
  }
  .brand-name {
    font-family: "Pathway Gothic One", sans-serif;
    font-size: 54px; color: var(--silver); letter-spacing: 1px;
  }
  .front-rule {
    position: absolute; left: 160px; top: 264px; width: 436px; height: 2px;
    background: var(--amber);
  }
  .front-title {
    position: absolute; left: 0; top: 276px; width: 100%; text-align: center;
    font-family: "Cinzel", serif; font-weight: 700;
    font-size: 32px; color: var(--teal); letter-spacing: 2px; text-transform: uppercase;
  }
  .back-rule {
    position: absolute; left: 160px; top: 100px; width: 2px; height: 252px;
    background: var(--amber);
  }
  .contact {
    position: absolute; left: 186px; top: 96px;
    font-family: "Pathway Gothic One", sans-serif; font-size: 18px; line-height: 21px;
  }
  .contact__primary { color: var(--amber); }
  .contact__address { color: var(--grey-text); margin-top: 28px; line-height: 23px; }
  .contact__lines { margin-top: 30px; line-height: 24px; }
  .contact__label { color: var(--amber); }
  .contact__value { color: var(--grey-text); }
  .back-brand {
    position: absolute; right: 26px; top: 150px;
    display: flex; align-items: center; gap: 12px;
  }
  .back-brand .brand-name { font-size: 46px; color: var(--faint); }
  .back-brand .brand-dot { background: var(--faint); }
</style>
</head>
<body>
<main class="canvas">
  <section class="card card--front" aria-label="Business card front">
    <div class="brand-lockup">
      <span class="brand-dot"></span>
      <span class="brand-name">Bright Pathwork</span>
    </div>
    <div class="front-rule"></div>
    <h1 class="front-title">Bright Pathwork</h1>
  </section>

  <section class="card card--back" aria-label="Business card back">
    <div class="back-rule"></div>
    <div class="contact">
      <div class="contact__primary">
        <p>Dana Ridley - Director</p>
        <p>Brightpathwork.com.au</p>
        <p>Dana@brightpathwork.com.au</p>
      </div>
      <div class="contact__address">
        <p>Level 14</p>
        <p>Harbourline House</p>
        <p>88 &nbsp; Kent Lane</p>
        <p>Millers Point, Sydney 2000</p>
      </div>
      <div class="contact__lines">
        <p><span class="contact__label">Tel</span> <span class="contact__value">---------------- (02) &nbsp;55501234</span></p>
        <p><span class="contact__label">Fax</span> <span class="contact__value">--------------- (02) &nbsp;55501288</span></p>
      </div>
    </div>
    <div class="back-brand">
      <span class="brand-dot"></span>
      <span class="brand-name">Bright Pathwork</span>
    </div>
  </section>
</main>
</body>
</html>
```